Tidy paddock Services

After a high quality design website. we are a company that provides services to people that own land and need a hand getting on top of the delayed jobs.
would want a number of tab/ pages for the web page.
Home page / About us page / services page / Gallery page. / Contact us page
we offer a wide range of services .listed below

Stock Work (title)

Stock movement
Break feeding
Temporary staffing

Spraying (title)

Spraying weeds
Spraying gorse

Pastures (title)

Fertilizing
Topping

Building (title)

Habitable sheds
Farm sheds
Sheep yards
Cattle yards
Repair farm buildings
Decks
Retaining walls

Fencing (title)

Stock fencing
Post & rail
Stock yards repair
Electric fencing install & repairs

Water Management (title)

Water trough installation
Water scheme install
Water trough cleaning
Farm water maintenance
Water ponds
Ornamental ponds
Drainage

General (title)

Lawn mowing
Hedge trimming
Pruning trees
Metaling drive ways & races
Water blasting
Small digger work
Little tip truck cartage
Home kill management
Mulching gorse
Section clearing

```html
<!DOCTYPE html>
<html lang="en">
<head>
<meta charset="utf-8">
<title>Tidy paddock Services</title>
<link href="https://fonts.googleapis.com/css2?family=Nunito:wght@400;500;600;700;800&display=swap" rel="stylesheet">
<style>
:root{
  --green:#6b9b1e;
  --green-dark:#5a8617;
  --ink:#111111;
  --text:#333333;
  --muted:#666666;
  --line:#d9d9d9;
  --soft:#f4f3f3;
  --white:#ffffff;
  --black:#000000;
}
*{box-sizing:border-box;margin:0;padding:0}
html,body{width:1200px;height:3484px;overflow:hidden}
body{position:relative;font-family:"Nunito",sans-serif;color:var(--ink);background:var(--white)}
.abs{position:absolute}
.btn{position:absolute;display:flex;align-items:center;justify-content:center;background:var(--green);color:var(--white);border-radius:30px;font-weight:600;letter-spacing:.2px}
.section-title{position:absolute;left:0;width:1200px;text-align:center;font-weight:800;font-size:32px;letter-spacing:-.3px;color:var(--ink)}
.rule{position:absolute;height:3px;width:40px;background:var(--green)}

/* hero */
.hero-photo{left:0;top:0;width:1200px;height:700px;background:linear-gradient(180deg,#8fb8d8 0%,#c9dbe4 22%,#e4e6da 34%,#9cab6a 46%,#6f8f34 58%,#86a834 78%,#7a9a2c 100%)}
.brand{position:absolute;display:flex;align-items:center;gap:10px;font-weight:800;color:var(--green);white-space:nowrap}
.brand-dot{width:14px;height:14px;border-radius:50%;background:var(--green)}
.nav{position:absolute;top:37px;left:0;width:1200px;height:36px}
.nav a{position:absolute;top:0;height:36px;line-height:36px;font-size:14.5px;color:var(--ink);text-decoration:none;font-weight:500}
.nav a.active{background:var(--green);color:var(--white);border-radius:8px;padding:0 14px}
.hero-welcome{left:0;width:1200px;top:166px;text-align:center;font-size:44px;font-weight:800;color:var(--ink);letter-spacing:-.5px}
.hero-name{left:0;width:1200px;top:222px;text-align:center;font-size:46px;font-weight:800;color:var(--green);letter-spacing:-.5px}
.hero-lead{left:250px;width:700px;top:292px;text-align:center;font-size:17px;line-height:26px;color:var(--ink)}
.dots{left:562px;top:595px;display:flex;gap:17px}
.dots span{width:14px;height:14px;border-radius:50%;background:var(--white)}
.dots span.ring{background:transparent;border:2px solid var(--white)}

/* services */
.card{position:absolute;top:896px;width:223px;height:346px;border:1px solid var(--line);border-radius:18px;background:var(--white)}
.card-photo{position:absolute;top:855px;width:223px;height:227px}
.card h3{position:absolute;left:28px;top:208px;font-size:13px;font-weight:800;color:var(--ink)}
.card ul{position:absolute;left:28px;top:234px;list-style:none}
.card li{position:relative;padding-left:15px;font-size:12.5px;height:24px;line-height:24px;color:var(--text)}
.card li::before{content:"";position:absolute;left:0;top:8px;border-left:5px solid var(--green);border-top:4px solid transparent;border-bottom:4px solid transparent}
.chev{position:absolute}

/* about */
.about-bg{left:586px;top:1394px;width:614px;height:520px;background:var(--soft)}
.about-photo{left:0;top:1394px;width:586px;height:540px;background:linear-gradient(180deg,#3d5a24 0%,#5e7a2c 28%,#8aa24a 45%,#7fa336 70%,#6f9a2a 100%)}
.about-copy{left:643px;top:1543px;width:436px;font-size:14.5px;line-height:25.7px;color:var(--text);text-align:justify}

/* gallery */
.shot{position:absolute;top:2104px;width:276px;height:254px;border-radius:16px}

/* contact */
.contact-bg{left:0;top:2523px;width:1200px;height:620px;background:linear-gradient(180deg,#f5f5f5 0%,#f5f5f5 55%,#e6e7de 70%,#c9cfb2 85%,#b4c08a 100%)}
.field{position:absolute;border:1px solid #8a8a8a;border-radius:22px;background:rgba(255,255,255,.35);font-size:13.5px;color:var(--muted);padding:0 26px;display:flex;align-items:center}
.field.tall{align-items:flex-start;padding-top:14px;border-radius:24px}

/* footer */
.footer-bg{left:0;top:3130px;width:1200px;height:354px;background:var(--black)}
.footer-text{color:var(--white);font-size:15px;line-height:23px}
.footer-nav a{position:absolute;top:3286px;font-size:14.5px;color:var(--white);text-decoration:none}
</style>
</head>
<body>

<!-- Hero -->
<div class="abs hero-photo" role="img" aria-label="Sunlit green farm paddocks with fences, trees and a stock trailer under a blue sky"></div>
<svg class="abs" style="left:0;top:590px" width="1200" height="130" viewBox="0 0 1200 130">
  <defs>
    <linearGradient id="heroStrip" x1="0" x2="1" y1="0" y2="0">
      <stop offset="0" stop-color="#000"/><stop offset=".5" stop-color="#000"/><stop offset=".62" stop-color="#6b9b1e"/><stop offset="1" stop-color="#6b9b1e"/>
    </linearGradient>
  </defs>
  <path d="M0,72 C150,100 400,82 650,45 C850,18 1050,26 1200,72 L1200,100 C1050,48 850,32 650,50 C450,70 200,125 0,102Z" fill="url(#heroStrip)"/>
  <path d="M0,102 C200,125 450,70 650,50 C850,32 1050,48 1200,100 L1200,130 L0,130Z" fill="#fff"/>
</svg>

<div class="brand" style="left:135px;top:62px;font-size:26px"><span class="brand-dot"></span>Tidy paddock Services</div>

<nav class="nav">
  <a class="active" style="left:564px">HOME</a>
  <a style="left:660px">ABOUT US</a>
  <a style="left:768px">SERVICES</a>
  <a style="left:871px">GALLERY</a>
  <a style="left:966px">CONTACT US</a>
</nav>

<div class="abs hero-welcome">WELCOME TO</div>
<div class="abs hero-name">TIDY PADDOCK SERVICES</div>
<p class="abs hero-lead">Lorem ipsum dolor sit amet, consectetur adipiscing elit, sed do eiusmod tempor&nbsp; incididunt ut labore et dolore magna aliqua.</p>
<div class="btn" style="left:511px;top:384px;width:176px;height:49px;font-size:18px">READ MORE</div>
<div class="abs dots"><span></span><span class="ring"></span><span></span></div>

<!-- Services -->
<h2 class="section-title" style="top:733px">OUR SERVICES</h2>
<div class="rule" style="left:580px;top:804px"></div>

<svg class="chev" style="left:54px;top:1048px" width="34" height="60" viewBox="0 0 34 60"><path d="M30,2 L4,30 L30,58" fill="none" stroke="#bbb" stroke-width="3"/></svg>
<svg class="chev" style="left:1112px;top:1048px" width="34" height="60" viewBox="0 0 34 60"><path d="M4,2 L30,30 L4,58" fill="none" stroke="#bbb" stroke-width="3"/></svg>

<div class="card" style="left:133px">
  <h3>STOCK WORK</h3>
  <ul><li>Stock movement</li><li>Break feeding</li><li>Temporary staffing</li></ul>
</div>
<div class="card" style="left:371px">
  <h3>SPRAYING</h3>
  <ul><li>Spraying weeds</li><li>Spraying gorse</li></ul>
</div>
<div class="card" style="left:607px">
  <h3>PASTURES</h3>
  <ul><li>Fertilizing</li><li>Topping</li></ul>
</div>
<div class="card" style="left:844px">
  <h3 style="top:204px">FENCING</h3>
  <ul style="top:230px"><li>Stock fencing</li><li>Post &amp; rail</li><li>Stock yards repair</li><li>Electric fencing install &amp; repairs</li></ul>
</div>

<svg class="card-photo" style="left:133px" viewBox="0 0 223 227" role="img" aria-label="Farm team meeting around a table">
  <defs><linearGradient id="g1" x1="0" y1="0" x2="0" y2="1"><stop offset="0" stop-color="#dfe3e2"/><stop offset="1" stop-color="#6f6a63"/></linearGradient></defs>
  <path d="M0,59 Q0,41 18,41 H50 A61.5 61.5 0 0 1 173,41 H205 Q223,41 223,59 V227 H0Z" fill="url(#g1)"/>
</svg>
<svg class="card-photo" style="left:371px" viewBox="0 0 223 227" role="img" aria-label="Tractor spraying a crop field at sunset">
  <defs><linearGradient id="g2" x1="0" y1="0" x2="0" y2="1"><stop offset="0" stop-color="#d9b765"/><stop offset=".5" stop-color="#8a8a3a"/><stop offset="1" stop-color="#3f5a1f"/></linearGradient></defs>
  <path d="M0,59 Q0,41 18,41 H50 A61.5 61.5 0 0 1 173,41 H205 Q223,41 223,59 V227 H0Z" fill="url(#g2)"/>
</svg>
<svg class="card-photo" style="left:607px" viewBox="0 0 223 227" role="img" aria-label="Cattle grazing a misty pasture at sunrise">
  <defs><linearGradient id="g3" x1="0" y1="0" x2="0" y2="1"><stop offset="0" stop-color="#e0a45e"/><stop offset=".55" stop-color="#8b6a45"/><stop offset="1" stop-color="#3b3324"/></linearGradient></defs>
  <path d="M0,59 Q0,41 18,41 H50 A61.5 61.5 0 0 1 173,41 H205 Q223,41 223,59 V227 H0Z" fill="url(#g3)"/>
</svg>
<svg class="card-photo" style="left:844px" viewBox="0 0 223 227" role="img" aria-label="Black metal fence along a lawn">
  <defs><linearGradient id="g4" x1="0" y1="0" x2="0" y2="1"><stop offset="0" stop-color="#cfd8d2"/><stop offset=".5" stop-color="#5e6b4a"/><stop offset="1" stop-color="#9a7a5e"/></linearGradient></defs>
  <path d="M0,59 Q0,41 18,41 H50 A61.5 61.5 0 0 1 173,41 H205 Q223,41 223,59 V227 H0Z" fill="url(#g4)"/>
</svg>

<div class="btn" style="left:503px;top:1287px;width:197px;height:50px;font-size:15px">VIEW ALL SERVICES</div>

<!-- About -->
<div class="abs about-bg"></div>
<div class="abs about-photo" role="img" aria-label="White barn with blue roof on a green hillside below autumn woods"></div>
<h2 class="abs" style="left:643px;top:1447px;font-size:32px;font-weight:800;letter-spacing:-.3px">ABOUT US</h2>
<div class="rule" style="left:643px;top:1509px"></div>
<p class="abs about-copy">At vero eos et accusamus et iusto odio dignissimos ducimus qui blanditiis praesentium voluptatum deleniti atque corrupti quos dolores et quas molestias excepturi sint occaecati cupiditate non provident, similique sunt in culpa qui officia deserunt mollitia animi, id est laborum et dolorum fuga. Et harum quidem rerum facilis est et expedita distinctio. Nam libero tempore, cum soluta nobis est eligendi optio cumque nihil impedit quo minus id</p>
<div class="btn" style="left:644px;top:1759px;width:143px;height:50px;font-size:15px">READ MORE</div>

<svg class="abs" style="left:0;top:1850px" width="1200" height="100" viewBox="0 0 1200 100">
  <path d="M0,68 C200,85 450,60 700,30 C900,8 1080,14 1200,40 L1200,72 C1080,34 900,22 700,38 C450,66 200,100 0,84Z" fill="#6b9b1e"/>
  <path d="M0,84 C200,100 450,66 700,38 C900,22 1080,34 1200,72 L1200,100 L0,100Z" fill="#fff"/>
</svg>

<!-- Gallery -->
<h2 class="section-title" style="top:1974px">GALLERY</h2>
<div class="rule" style="left:580px;top:2045px"></div>
<div class="shot" style="left:28px;background:linear-gradient(180deg,#7fa3cc 0%,#e2e8ec 45%,#6f9440 62%,#4f7a2a 100%)" role="img" aria-label="Wooden fence beside an open green field under a cloudy sky"></div>
<div class="shot" style="left:321px;background:linear-gradient(180deg,#d8cf86 0%,#8fae4a 45%,#5f8a2c 100%)" role="img" aria-label="Lawn mower cutting grass in the sun"></div>
<div class="shot" style="left:613px;background:linear-gradient(180deg,#5b7a9a 0%,#4f7a28 35%,#3f6a1e 100%)" role="img" aria-label="Hedge being trimmed with shears"></div>
<div class="shot" style="left:906px;background:linear-gradient(135deg,#6b6b6b 0%,#9a9a9a 40%,#8a5a5e 70%,#6e6e6e 100%)" role="img" aria-label="Paving stones being laid beside a drain grate"></div>
<svg class="chev" style="left:70px;top:2200px" width="28" height="52" viewBox="0 0 28 52"><path d="M25,2 L3,26 L25,50" fill="none" stroke="#fff" stroke-width="3"/></svg>
<svg class="chev" style="left:1116px;top:2200px" width="28" height="52" viewBox="0 0 28 52"><path d="M3,2 L25,26 L3,50" fill="none" stroke="#fff" stroke-width="3"/></svg>
<div class="btn" style="left:518px;top:2404px;width:182px;height:49px;font-size:15px">VIEW ALL IMAGES</div>

<!-- Contact -->
<div class="abs contact-bg" role="img" aria-label="Faded misty farm landscape behind the contact form"></div>
<h2 class="section-title" style="top:2570px">CONTACT US</h2>
<div class="rule" style="left:580px;top:2640px"></div>
<div class="field" style="left:202px;top:2692px;width:381px;height:53px">First Name</div>
<div class="field" style="left:603px;top:2692px;width:382px;height:53px">Last Name</div>
<div class="field" style="left:202px;top:2771px;width:381px;height:53px">Email id</div>
<div class="field" style="left:603px;top:2771px;width:382px;height:53px">Phone</div>
<div class="field tall" style="left:202px;top:2848px;width:783px;height:115px">Message</div>
<div class="btn" style="left:509px;top:2989px;width:168px;height:53px;font-size:20px;font-weight:800">SUBMIT</div>

<!-- Footer -->
<div class="abs footer-bg"></div>
<svg class="abs" style="left:0;top:3060px" width="1200" height="90" viewBox="0 0 1200 90">
  <path d="M0,62 C200,82 450,50 700,28 C900,12 1080,16 1200,40 L1200,62 C1080,34 900,30 700,42 C450,62 200,92 0,80Z" fill="#6b9b1e"/>
  <path d="M0,80 C200,92 450,62 700,42 C900,30 1080,34 1200,62 L1200,90 L0,90Z" fill="#000"/>
</svg>

<div class="brand" style="left:131px;top:3243px;font-size:30px"><span class="brand-dot" style="width:16px;height:16px"></span>Tidy paddock Services</div>
<div class="abs" style="left:536px;top:3200px;width:1px;height:121px;background:#777"></div>

<svg class="abs" style="left:606px;top:3210px" width="28" height="28" viewBox="0 0 24 24" fill="none" stroke="#fff" stroke-width="1.3"><path d="M5,3 L9,3 L10.5,7.5 L8.5,9 C9.5,11.5 12.5,14.5 15,15.5 L16.5,13.5 L21,15 L21,19 C21,20 20,21 19,21 C10,20.5 3.5,14 3,5 C3,4 4,3 5,3Z"/><path d="M14,3 C17.5,3.5 20.5,6.5 21,10"/><path d="M14,6.5 C16,7 17,8 17.5,10"/></svg>
<div class="abs footer-text" style="left:649px;top:3201px">Call Us<br>+1 555 010 2030</div>

<svg class="abs" style="left:814px;top:3212px" width="28" height="22" viewBox="0 0 28 22" fill="none" stroke="#fff" stroke-width="1.4"><rect x="1" y="1" width="26" height="20"/><path d="M1,1 L14,12 L27,1"/><path d="M1,21 L10,9"/><path d="M27,21 L18,9"/></svg>
<div class="abs footer-text" style="left:860px;top:3197px">Email Us<br>info@tidypaddockservices.com</div>

<nav class="footer-nav">
  <a style="left:606px">HOME</a>
  <a style="left:686px">ABOUT US</a>
  <a style="left:789px">SERVICES</a>
  <a style="left:890px">GALLERY</a>
  <a style="left:982px">CONTACT US</a>
</nav>

<div class="abs" style="left:133px;top:3365px;width:936px;height:1px;background:#444"></div>
<div class="abs" style="left:0;top:3411px;width:1200px;text-align:center;font-size:13px;color:#ddd">Copyright © 2024 All Rights Reserved</div>

</body>
</html>
```